Brantor Works Business Card

Modern and Professional Business Card for a Med size construction/development company.

See the samples below for the design I like … but I need ideas for incorporating the red company logo while still keeping the clean look of the card samples that are attached.

Logo and tag line on the back … info on the front.

Tagline: Strength Built from the Footing Up

Target Market(s)

Med-Large General Contractors

Contact Information for Business Card

Brantor Works Limited
42 Fenwick Avenue
Mt. Pearl, NL
A1N 4R9

t: 709-555-0147
f: 709-555-0182
w: www.brantorworks-example.com

Font styles to use
Sans Serif

Colors
fbee3e

Requirements
Must have
• I like the black and yellow designs of the attached samples …. but I'm not sure how to incorporate the red Brantor Works logo into that design??
Nice to have
• Construction safety strips

```html
<!DOCTYPE html>
<html lang="en">
<head>
<meta charset="utf-8">
<title>Brantor Works Business Card</title>
<link rel="stylesheet" href="https://fonts.googleapis.com/css2?family=Lato:wght@400;700;900&display=swap">
<style>
  :root {
    --bg: #1c1c1d;
    --card: #0b0c0d;
    --red: #e3202a;
    --white: #f2f2f2;
    --rule: #4a4a4a;
    --tread-a: #141516;
    --tread-b: #0b0c0d;
  }
  * { margin: 0; padding: 0; box-sizing: border-box; }
  html, body { width: 1200px; height: 1108px; overflow: hidden; }
  body {
    background: var(--bg);
    font-family: "Lato", Arial, sans-serif;
    color: var(--white);
    position: relative;
  }
  .card {
    position: absolute;
    top: 154px;
    width: 457px;
    height: 800px;
    background: var(--card);
    border-radius: 22px;
    overflow: hidden;
  }
  .card--front { left: 113px; }
  .card--back { left: 630px; }

  .brand-name {
    font-weight: 900;
    color: var(--red);
    text-align: center;
    letter-spacing: 1px;
    line-height: 1;
  }
  .card--front .brand-name { margin-top: 140px; font-size: 44px; }

  .person { text-align: center; margin-top: 150px; }
  .person__name { font-weight: 700; font-size: 36px; color: var(--red); letter-spacing: 1px; }
  .person__title { font-size: 22px; margin-top: 8px; }

  .divider {
    position: relative;
    width: 300px;
    height: 1px;
    background: var(--rule);
    margin: 26px auto 0;
  }
  .contact-icons {
    position: absolute;
    left: 50%;
    top: -14px;
    transform: translateX(-50%);
    display: flex;
    gap: 6px;
    background: var(--card);
    padding: 0 8px;
  }
  .contact-icons svg { width: 28px; height: 28px; display: block; }

  .contact { text-align: center; margin-top: 30px; font-size: 22px; line-height: 1.5; }
  .contact__web { font-size: 20px; }

  .address { text-align: center; margin-top: 4px; font-size: 21px; line-height: 1.35; }
  .address__company { color: var(--red); margin-top: 20px; }

  .tread {
    position: absolute;
    inset: 0 0 230px 0;
    background: linear-gradient(180deg, var(--tread-a) 0%, var(--tread-b) 100%);
  }
  .back-brand { position: absolute; left: 0; right: 0; bottom: 120px; }
  .card--back .brand-name { font-size: 48px; }
  .back-rule { width: 340px; height: 1px; background: var(--rule); margin: 18px auto 0; }
  .tagline {
    text-align: center;
    font-size: 16px;
    letter-spacing: 1.5px;
    text-transform: uppercase;
    margin-top: 14px;
  }
</style>
</head>
<body>
  <section class="card card--front">
    <p class="brand-name">BRANTOR WORKS</p>

    <div class="person">
      <p class="person__name">DANA WHITLOCK</p>
      <p class="person__title">Founder &amp; CEO</p>
    </div>

    <div class="divider">
      <div class="contact-icons">
        <svg viewBox="0 0 28 28" aria-label="Phone">
          <circle cx="14" cy="14" r="13" fill="#e3202a"/>
          <path d="M9 8 l3 0 l1 4 l-2 1 q1.5 3 4 4 l1 -2 l4 1 l0 3 q-9 0 -11 -11z" fill="#0b0c0d"/>
        </svg>
        <svg viewBox="0 0 28 28" aria-label="Fax">
          <circle cx="14" cy="14" r="13" fill="#e3202a"/>
          <rect x="10" y="7" width="8" height="5" fill="#0b0c0d"/>
          <rect x="7" y="12" width="14" height="7" rx="1" fill="#0b0c0d"/>
          <rect x="10" y="17" width="8" height="4" fill="#0b0c0d"/>
        </svg>
        <svg viewBox="0 0 28 28" aria-label="Website">
          <circle cx="14" cy="14" r="13" fill="#e3202a"/>
          <circle cx="14" cy="14" r="7" fill="none" stroke="#0b0c0d" stroke-width="1.6"/>
          <ellipse cx="14" cy="14" rx="3" ry="7" fill="none" stroke="#0b0c0d" stroke-width="1.4"/>
          <line x1="7" y1="14" x2="21" y2="14" stroke="#0b0c0d" stroke-width="1.4"/>
        </svg>
      </div>
    </div>

    <div class="contact">
      <p>709-555-0147</p>
      <p>709-555-0182</p>
      <p class="contact__web">www.brantorworks-example.com</p>
    </div>

    <div class="divider"></div>

    <div class="address">
      <p class="address__company">Brantor Works Limited</p>
      <p>42 Fenwick Avenue Harbour</p>
      <p>Ridge, NL A0B 2C3</p>
    </div>
  </section>

  <section class="card card--back">
    <div class="tread" role="img" aria-label="Faint tyre tread pattern"></div>
    <div class="back-brand">
      <p class="brand-name">BRANTOR WORKS</p>
      <div class="back-rule"></div>
      <p class="tagline">Strength built from the footing up</p>
    </div>
  </section>
</body>
</html>
```